Modern Business Card for Larkwell 2018

Our company assumes the best about people. We are creating an online community of entrepreneurs and business leaders who struggle with marketing their business online.

This business card should POP! We recently got a new logo and are launching a new website next month, so our business cards should make a statement that feels:
-Fresh
-Smart
-Trustworthy
-Fun

Target Market(s)

small business owners, entrepreneurs

Industry/Entity Type

Digital Marketing

Contact Information for Business Card

Dimensions: 3.5" x 2"

Font styles to use
Sans Serif

Colors
f37122
ffffff

Requirements
Must have
• We need a business card with a modern, bold design. We will use one side of the card as a lead-generation offer, so text on one side will need to fit up to 140 characters. The business card should stick to our core colors (orange, black, and white).
Nice to have
• We think a vertical "portrait" design could be interesting.
Should not have
• Should not look like a traditional business card. The round icon should stand out from a distance.

```html
<!DOCTYPE html>
<html lang="en">
<head>
<meta charset="utf-8">
<title>Larkwell Business Card</title>
<link rel="stylesheet" href="https://fonts.googleapis.com/css2?family=Roboto:wght@400;500;700;900&family=Roboto+Condensed:wght@500;700&display=swap">
<style>
  :root {
    --orange: #f37122;
    --white: #ffffff;
    --paper: #f2f2f2;
    --ink: #222222;
    --muted: #555555;
    --faint: #f6dccd;
    --backdrop: #2b2b2b;
  }
  * { margin: 0; padding: 0; box-sizing: border-box; }
  html, body { width: 1200px; height: 960px; overflow: hidden; }
  body {
    position: relative;
    background: var(--backdrop);
    font-family: "Roboto", Arial, sans-serif;
  }
  .card {
    position: absolute;
    width: 600px;
    height: 342px;
    overflow: hidden;
  }

  /* Front */
  .card-front { left: 314px; top: 113px; background: var(--paper); }
  .front-accent-circle {
    position: absolute;
    left: 1px; top: 2px;
    width: 340px; height: 340px;
    border-radius: 50%;
    background: var(--faint);
    opacity: 0.7;
  }
  .name-marker {
    position: absolute;
    left: 0; top: 65px;
    width: 9px; height: 47px;
    background: var(--orange);
  }
  .person-name {
    position: absolute;
    left: 30px; top: 67px;
    font-family: "Roboto Condensed", "Arial Narrow", sans-serif;
    font-weight: 700;
    font-size: 24px;
    color: var(--orange);
    letter-spacing: 0.2px;
  }
  .person-role {
    position: absolute;
    left: 31px; top: 96px;
    font-size: 15.5px;
    font-weight: 400;
    color: var(--ink);
    letter-spacing: 0.3px;
  }
  .person-email {
    position: absolute;
    left: 30px; top: 274px;
    font-size: 14px;
    color: var(--muted);
  }
  .brand {
    position: absolute;
    left: 336px; top: 35px;
    width: 240px;
    text-align: center;
  }
  .brand-dot {
    display: block;
    width: 36px; height: 36px;
    margin: 0 auto 12px;
    border-radius: 50%;
    background: var(--orange);
  }
  .brand-name {
    display: block;
    font-weight: 900;
    font-size: 37px;
    line-height: 1;
    letter-spacing: 1.5px;
    color: var(--ink);
  }
  .brand-tagline {
    display: block;
    margin-top: 8px;
    font-size: 11.5px;
    font-weight: 700;
    letter-spacing: 0.6px;
    color: var(--ink);
  }

  /* Back */
  .card-back { left: 311px; top: 472px; background: var(--orange); color: var(--white); }
  .back-brand {
    position: absolute;
    left: 70px; top: 44px;
    width: 180px;
    text-align: center;
  }
  .back-brand-dot {
    display: block;
    width: 96px; height: 96px;
    margin: 0 auto 10px;
    border-radius: 50%;
    background: var(--white);
  }
  .back-brand-name {
    display: block;
    font-weight: 900;
    font-size: 26px;
    letter-spacing: 1px;
    color: var(--white);
  }
  .divider {
    position: absolute;
    left: 264px; top: 30px;
    width: 1px; height: 168px;
    background: var(--white);
    opacity: 0.8;
  }
  .offer {
    position: absolute;
    left: 297px; top: 31px;
    width: 290px;
  }
  .offer-headline {
    font-size: 19.5px;
    font-weight: 700;
    line-height: 21px;
    text-transform: uppercase;
  }
  .offer-body {
    margin-top: 6px;
    font-size: 15px;
    line-height: 19px;
  }
  .offer-url {
    margin-top: 8px;
    font-size: 19px;
    font-weight: 700;
  }
  .notes-box {
    position: absolute;
    left: 20px; top: 217px;
    width: 557px; height: 101px;
    background: var(--white);
    border-radius: 16px;
  }
  .notes-line {
    position: absolute;
    left: 24px; right: 27px;
    height: 1px;
    background: var(--ink);
  }
  .notes-line-1 { top: 31px; }
  .notes-line-2 { top: 71px; }
</style>
</head>
<body>
  <section class="card card-front" aria-label="Card front">
    <div class="front-accent-circle" aria-hidden="true"></div>
    <div class="name-marker" aria-hidden="true"></div>
    <h1 class="person-name">REID CALLOWAY</h1>
    <p class="person-role">STORY MARKETING COACH</p>
    <p class="person-email">reid@larkwellnow.com</p>
    <div class="brand">
      <span class="brand-dot" aria-hidden="true"></span>
      <span class="brand-name">LARKWELL</span>
      <span class="brand-tagline">SHARE STORIES THAT SPARK GROWTH</span>
    </div>
  </section>

  <section class="card card-back" aria-label="Card back">
    <div class="back-brand">
      <span class="back-brand-dot" aria-hidden="true"></span>
      <span class="back-brand-name">LARKWELL</span>
    </div>
    <div class="divider" aria-hidden="true"></div>
    <div class="offer">
      <p class="offer-headline">Reach more people.<br>Make more money.<br>Create more impact.</p>
      <p class="offer-body">Get your free Larkwell<br>Starter Package and our<br>marketing guide today at</p>
      <p class="offer-url">Larkwellnow.com/start</p>
    </div>
    <div class="notes-box">
      <div class="notes-line notes-line-1"></div>
      <div class="notes-line notes-line-2"></div>
    </div>
  </section>
</body>
</html>
```